Landing-Page-Design für Immobilienunternehmen
Zielgruppe
Die Firma Kalmt Immobilien kauft jegliche Art von Immobilien im Osten von Hamburg. Die Zielgruppe sind Immobilienbesitzer, welche ihre Wohnung, Haus, Gewerbe oder Sonstiges verkaufen möchten/müssen.
Ich würde gerne drei Unterzielgruppe mehr ansprechen:
Verkauf weil geerbt
textlich untermauert
Verkauf weil ins Altersheim
Verkauf weil ein Geldengpass
Wir kaufen:
Häuser
Eigentumswohnungen
Gewerbeflächen
Mehrfamilienhäuser
Garagen
Agrarflächen (Wald, Acker, Wiese, Teiche)
Aufgabenstellung
Es besteht ein Logo, welches berücksichtigt werden müsste.
Außerdem:
- responsive
- seriös
- conversion optimiert
- viel bebildert, textliche untermauert
- vertrauensvoll/verschwiegen
Telefonnummer soll prominent dargestellt werden, genauso wie ein Kontaktformular.

```html
<!DOCTYPE html>
<html lang="de">
<head>
<meta charset="utf-8">
<title>Kalmt Immobilien – Wir kaufen Immobilien</title>
<link href="https://fonts.googleapis.com/css2?family=Roboto:wght@300;400;500&family=Roboto+Condensed:wght@300;400&family=Arimo:wght@700&display=swap" rel="stylesheet">
<style>
:root{
  --green:#82bc2a;
  --green-dark:#6fa321;
  --ink:#3a3d42;
  --text:#666;
  --grey-band:#f3f3f3;
  --card:#f4f4f4;
  --footer:#1a1a1a;
  --white:#fff;
}
*{margin:0;padding:0;box-sizing:border-box}
html,body{width:1200px;height:2803px;overflow:hidden;background:var(--white);font-family:"Roboto",Arial,sans-serif}
.page{position:relative;width:1200px;height:2803px;overflow:hidden}
.abs{position:absolute}

/* header */
.brand{left:145px;top:150px;width:560px;text-align:center}
.brand-mark{display:inline-block;width:60px;height:60px;background:var(--green);margin-bottom:22px}
.brand-name{font-family:"Roboto",sans-serif;font-weight:500;font-size:46px;letter-spacing:3px;color:var(--ink);line-height:1}
.brand-tag{font-family:"Roboto",sans-serif;font-weight:400;font-size:19px;letter-spacing:2px;color:var(--ink);margin-top:14px}
.claim{left:715px;top:22px;width:490px;height:270px}
.claim-text{left:760px;top:70px;width:420px;transform:rotate(-6deg);font-family:"Arimo",sans-serif;font-weight:700;font-size:36px;line-height:38px;color:var(--white);text-align:center}

/* headings */
.section-title{left:0;width:1182px;text-align:center;font-family:"Roboto Condensed",sans-serif;font-weight:300;font-size:34px;color:var(--green)}
.section-sub{left:0;width:1182px;text-align:center;font-family:"Roboto Condensed",sans-serif;font-weight:300;font-size:25px;color:var(--ink)}

/* reason cards */
.card{top:491px;width:339px;height:537px;background:var(--card)}
.card-head{height:48px;background:var(--green);color:var(--white);font-family:"Roboto Condensed",sans-serif;font-size:23px;letter-spacing:2px;text-align:center;line-height:48px}
.card-photo{height:223px}
.card-body{padding:28px 32px 0;font-family:"Roboto",sans-serif;font-weight:300;font-size:20.5px;line-height:27.5px;color:var(--text);text-align:justify;hyphens:auto}
.card-body .more{color:var(--green);font-weight:400;margin-left:18px}

/* call */
.call-flag{left:255px;top:1012px;width:240px;height:130px}
.call-text{left:300px;top:1040px;width:150px;transform:rotate(-6deg);font-family:"Arimo",sans-serif;font-weight:700;font-size:23px;line-height:26px;color:var(--white);text-align:center}
.call-number{left:500px;top:1040px;font-family:"Arimo",sans-serif;font-weight:700;font-style:italic;font-size:40px;color:var(--green);letter-spacing:1px}

/* property types */
.band{left:0;top:1128px;width:1200px;height:965px;background:var(--grey-band)}
.type{top:1175px;width:200px;text-align:center}
.type-photo{height:199px}
.type-label{margin-top:14px;font-family:"Roboto",sans-serif;font-weight:300;font-size:25px;color:#222;white-space:nowrap;margin-left:-20px;margin-right:-20px}
.type-btn{display:inline-block;margin-top:12px;width:92px;height:26px;background:var(--green);border:2px solid #e2e2e2;color:var(--white);font-size:17px;line-height:22px;font-weight:300}
.arrow{top:1253px;width:24px;height:40px}

/* offer form */
.offer{left:0;top:1460px;width:1200px;height:640px}
.offer-title{left:60px;top:1575px;width:680px;transform:rotate(-5deg);font-family:"Arimo",sans-serif;font-weight:700;font-size:58px;line-height:60px;color:var(--white);text-align:center}
.field{height:45px;background:var(--white);font-family:"Roboto",sans-serif;font-weight:300;font-size:22px;color:#aaa;padding-left:24px;line-height:45px}
.submit{left:200px;top:1977px;width:342px;height:45px;border-radius:23px;background:#9a9a9a;color:var(--white);font-family:"Roboto",sans-serif;font-weight:500;font-size:17px;text-align:center;line-height:45px}

/* gallery */
.tile{position:absolute}

/* footer */
.footer{left:0;top:2619px;width:1200px;height:184px;background:var(--footer)}
.foot-brand{left:540px;top:2710px;width:290px;text-align:center}
.foot-brand .brand-mark{width:22px;height:22px;margin-bottom:8px}
.foot-brand .brand-name{font-size:18px;color:var(--white);letter-spacing:1px}
.social{top:2680px;width:14px;height:14px;border-radius:50%;background:var(--white)}
.foot-links{left:0;top:2782px;width:1200px;text-align:center;font-family:"Roboto Condensed",sans-serif;font-size:10.5px;letter-spacing:1px;color:var(--white)}
.foot-rule{left:0;top:2776px;width:1200px;height:1px;background:#444}
</style>
</head>
<body>
<div class="page">

  <!-- Header -->
  <div class="abs brand">
    <span class="brand-mark"></span>
    <div class="brand-name">KALMT IMMOBILIEN</div>
    <div class="brand-tag">VERWALTUNG · BERATUNG · INVESTMENT</div>
  </div>
  <svg class="abs claim" viewBox="0 0 490 270" aria-hidden="true">
    <polygon points="8,56 480,4 465,178 377,190 345,205 90,218 98,262 28,222" fill="#82bc2a"/>
  </svg>
  <div class="abs claim-text">Wir kaufen Immobilien jeglicher Art im Osten von Hamburg!</div>

  <!-- Reasons -->
  <div class="abs section-title" style="top:392px">BEI UNS IST IHRE IMMOBILIE IN GUTER HAND</div>
  <div class="abs section-sub" style="top:436px">Egal, warum Sie verkaufen wollen!</div>

  <div class="abs card" style="left:67px">
    <div class="card-head">SIE HABEN GEERBT?</div>
    <div class="card-photo" role="img" aria-label="Ältere Hände halten ein kleines Holzhaus" style="background:linear-gradient(160deg,#c9ccd0,#a9aeb4)"></div>
    <p class="card-body">At vero eos et accusam et justo duo dolores et ea rebum. Stet clita kasd gubergren, no sea takimata sanctus est Lorem ipsum dolor sit amet. Lorem ipsum dolor sit amet, consetetur sadipscing elitr, sed diam nonu<span class="more">MEHR</span></p>
  </div>
  <div class="abs card" style="left:432px">
    <div class="card-head">SIE GEHEN INS ALTERSHEIM?</div>
    <div class="card-photo" role="img" aria-label="Nahaufnahme einer älteren Person" style="background:linear-gradient(90deg,#f6f6f6 35%,#d9c5b6)"></div>
    <p class="card-body">At vero eos et accusam et justo duo dolores et ea rebum. Stet clita kasd gubergren, no sea takimata sanctus est Lorem ipsum dolor sit amet. Lorem ipsum dolor sit amet, consetetur sadipscing elitr, sed diam nonu<span class="more">MEHR</span></p>
  </div>
  <div class="abs card" style="left:800px">
    <div class="card-head">SIE HABEN GELDENGPASS?</div>
    <div class="card-photo" role="img" aria-label="Ältere Frau blickt nachdenklich aus dem Fenster" style="background:linear-gradient(90deg,#e4e8ec,#8d949c)"></div>
    <p class="card-body">At vero eos et accusam et justo duo dolores et ea rebum. Stet clita kasd gubergren, no sea takimata sanctus est Lorem ipsum dolor sit amet. Lorem ipsum dolor sit amet, consetetur sadipscing elitr, sed diam nonu<span class="more">MEHR</span></p>
  </div>

  <!-- Property types -->
  <div class="abs band"></div>

  <svg class="abs call-flag" viewBox="0 0 240 130" aria-hidden="true">
    <polygon points="0,24 238,2 230,92 206,98 210,104 70,112 72,128 10,100" fill="#82bc2a"/>
  </svg>
  <div class="abs call-text">Rufen Sie uns an!</div>
  <div class="abs call-number">+49 4104 5550172</div>

  <svg class="abs arrow" style="left:20px" viewBox="0 0 24 40" aria-hidden="true"><polyline points="20,2 4,20 20,38" fill="none" stroke="#666" stroke-width="2"/></svg>
  <svg class="abs arrow" style="left:1153px" viewBox="0 0 24 40" aria-hidden="true"><polyline points="4,2 20,20 4,38" fill="none" stroke="#666" stroke-width="2"/></svg>

  <div class="abs type" style="left:74px">
    <div class="type-photo" role="img" aria-label="Weißes Einfamilienhaus mit rotem Dach" style="background:linear-gradient(#dfe6ee,#f2f2f2 55%,#7a8a5a)"></div>
    <div class="type-label">Häuser</div><span class="type-btn">MEHR</span>
  </div>
  <div class="abs type" style="left:292px">
    <div class="type-photo" role="img" aria-label="Helle, leere Eigentumswohnung mit Küche" style="background:linear-gradient(90deg,#f4f4f4,#d8d6d2)"></div>
    <div class="type-label">Eigentumswohnungen</div><span class="type-btn">MEHR</span>
  </div>
  <div class="abs type" style="left:511px">
    <div class="type-photo" role="img" aria-label="Luftbild eines Gewerbegebiets mit Hallen" style="background:linear-gradient(#5f8f3e,#b8bcc0 50%,#6a9a45)"></div>
    <div class="type-label">Gewerbeflächen</div><span class="type-btn">MEHR</span>
  </div>
  <div class="abs type" style="left:727px">
    <div class="type-photo" role="img" aria-label="Historisches Mehrfamilienhaus mit heller Fassade" style="background:linear-gradient(#cfdbe6,#ece9e2)"></div>
    <div class="type-label">Mehrfamilienhäuser</div><span class="type-btn">MEHR</span>
  </div>
  <div class="abs type" style="left:940px">
    <div class="type-photo" role="img" aria-label="Blaue Garage mit weißen Toren" style="background:linear-gradient(#9fb6cf,#3f5f8f 55%,#5a6e88)"></div>
    <div class="type-label">Garagen</div><span class="type-btn">MEHR</span>
  </div>

  <!-- Offer -->
  <svg class="abs offer" viewBox="0 0 1200 640" aria-hidden="true">
    <polygon points="0,128 832,40 767,540 700,572 650,600 0,634" fill="#82bc2a"/>
  </svg>
  <svg class="abs" style="left:767px;top:1463px" width="433" height="540" role="img" aria-label="Weißes Landhaus mit rotem Dach und Blumengarten">
    <defs><linearGradient id="houseTone" x1="0" y1="0" x2="0" y2="1"><stop offset="0" stop-color="#e8eef2"/><stop offset="0.6" stop-color="#d7d9d8"/><stop offset="1" stop-color="#6f6a5c"/></linearGradient></defs>
    <polygon points="65,36 433,0 433,495 0,539" fill="url(#houseTone)"/>
  </svg>
  <div class="abs offer-title">Fordern Sie Ihr individuelles Angebot an!</div>
  <div class="abs field" style="left:147px;top:1788px;width:486px">Vollständiger Name</div>
  <div class="abs field" style="left:147px;top:1842px;width:486px">Art der Immobilie</div>
  <div class="abs field" style="left:147px;top:1898px;width:209px">e-mail</div>
  <div class="abs field" style="left:423px;top:1898px;width:210px">Telefon</div>
  <div class="abs submit">Unverbindliches Angebot anfordern!</div>

  <!-- Gallery -->
  <div class="abs section-title" style="top:2104px">BEI UNS IST IHRE IMMOBILIE IN GUTER HAND</div>
  <div class="abs section-sub" style="top:2149px">Egal, warum Sie verkaufen wollen!</div>

  <div class="tile" style="left:27px;top:2200px;width:184px;height:185px;background:linear-gradient(#f0f0f0,#8a8a8a)" role="img" aria-label="Wohnzimmer im Dachgeschoss"></div>
  <div class="tile" style="left:220px;top:2193px;width:185px;height:192px;background:linear-gradient(135deg,#f2f2f2,#c9c9c9)" role="img" aria-label="Bebauungsplan mit Stift"></div>
  <div class="tile" style="left:410px;top:2193px;width:187px;height:192px;background:linear-gradient(#f2f4f6,#8ea07a)" role="img" aria-label="Weiße Stadtvilla"></div>
  <div class="tile" style="left:602px;top:2200px;width:377px;height:376px;background:linear-gradient(135deg,#2f5a30,#1c3b22 60%,#4d7a3a)" role="img" aria-label="Nadelwald von oben"></div>
  <div class="tile" style="left:987px;top:2200px;width:185px;height:185px;background:linear-gradient(#e7dfcf,#c8c0b0 35%,#6e4c3a)" role="img" aria-label="Gepflügter Acker"></div>
  <div class="tile" style="left:29px;top:2397px;width:182px;height:184px;background:linear-gradient(135deg,#6c9a4a,#9aa3ab,#7aa05a)" role="img" aria-label="Gewerbegebiet aus der Luft"></div>
  <div class="tile" style="left:220px;top:2393px;width:185px;height:188px;background:linear-gradient(#8fb4dc,#eeeeee 50%,#aaa)" role="img" aria-label="Modernes Mehrfamilienhaus"></div>
  <div class="tile" style="left:410px;top:2393px;width:187px;height:188px;background:linear-gradient(#dfe6e0,#6f8f4a 55%,#3d5a3a)" role="img" aria-label="Teich mit Seerosen und Wiese"></div>
  <div class="tile" style="left:987px;top:2397px;width:187px;height:184px;background:linear-gradient(#e6ebee,#cfd3d4 60%,#6f8a55)" role="img" aria-label="Moderne weiße Häuser"></div>

  <!-- Footer -->
  <div class="abs footer"></div>
  <div class="abs foot-brand">
    <span class="brand-mark"></span>
    <div class="brand-name">KALMT IMMOBILIEN</div>
  </div>
  <span class="abs social" style="left:886px"></span>
  <span class="abs social" style="left:916px"></span>
  <span class="abs social" style="left:946px"></span>
  <span class="abs social" style="left:976px"></span>
  <div class="abs foot-rule"></div>
  <div class="abs foot-links">KONTAKT &nbsp;|&nbsp; AGB &nbsp;|&nbsp; WIDERRUFSRECHT &nbsp;|&nbsp; ZAHLUNGSINFORMATION &nbsp;|&nbsp; DATENSCHUTZ &nbsp;|&nbsp; IMPRESSUM</div>

</div>
</body>
</html>
```